Business Card Design for Flood Rescue 360 - Property Restoration Professionals

I need a business card designed for Flood Rescue 360. We are a full-service property restoration solution. Providing water, fire, smoke & storm restoration as well as mold remediation and full remodel or reconstruction to homes and businesses across Dallas-Fort Worth, TX.
Target Market(s)
home and business owners with insurance covered property damage from water, fire or storm related damage
Industry/Entity Type
property restoration
Contact Information for Business Card
Marcus Pelley General Manager Cell: 214-555-0193 Office: 469-555-0148 email: Marcus@FloodRescue360.example services: Water, Fire, Mold, Reconstruction Tagline: Urgency for Your Water Emergency!
Look and feel
Each slider illustrates characteristics of the customer's brand and the style your logo design should communicate.

```html
<!DOCTYPE html>
<html lang="en">
<head>
<meta charset="utf-8">
<title>Flood Rescue 360 – Business Card</title>
<link href="https://fonts.googleapis.com/css2?family=Montserrat:wght@400;600;800&display=swap" rel="stylesheet">
<style>
  :root{
    --bg:#474747;
    --card:#161616;
    --blue:#00b0e6;
    --white:#ffffff;
  }
  *{margin:0;padding:0;box-sizing:border-box}
  html,body{width:1200px;height:801px;overflow:hidden}
  body{
    background:radial-gradient(ellipse at 40% 20%,#5a5a5a,var(--bg) 60%,#3a3a3a);
    font-family:'Montserrat',sans-serif;
    position:relative;
  }
  .card{
    position:absolute;
    width:540px;height:309px;
    background:var(--card);
    border-bottom:3px solid var(--blue);
    border-right:3px solid var(--blue);
    box-shadow:0 18px 40px rgba(0,0,0,.45);
    overflow:hidden;
  }
  .card--back{left:40px;top:246px}
  .card--front{left:620px;top:246px}

  /* back side */
  .brand-name{
    color:var(--blue);font-weight:600;white-space:nowrap;
  }
  .brand-name--small{
    position:absolute;left:30px;top:108px;font-size:19px;
  }
  .divider{
    position:absolute;left:262px;top:34px;width:1.5px;height:172px;background:var(--blue);
  }
  .contact{position:absolute;left:284px;top:32px;color:var(--white)}
  .contact__name{color:var(--blue);font-weight:800;font-size:22px;line-height:1.1}
  .contact__title{font-size:12.5px;margin:2px 0 12px}
  .contact__list{list-style:none;font-size:12.5px}
  .contact__list li{display:flex;align-items:center;gap:7px;height:20px}
  .contact__list svg{width:12px;height:12px;flex:none;fill:var(--blue)}
  .tagline{
    position:absolute;left:0;right:0;bottom:34px;text-align:center;
    color:var(--white);font-size:14.5px;letter-spacing:.3px;
  }

  /* front side */
  .brand-name--large{
    position:absolute;left:0;right:0;top:82px;text-align:center;font-size:40px;
  }
  .services{position:absolute;left:0;right:0;top:205px;text-align:center}
  .services__label{color:var(--blue);font-weight:800;font-size:17px;letter-spacing:.5px}
  .services__list{
    margin-top:12px;color:var(--white);font-size:16px;
    display:flex;justify-content:center;align-items:center;gap:9px;
  }
  .services__sep{width:7px;height:7px;border-radius:50%;background:var(--blue)}
</style>
</head>
<body>

<section class="card card--back" aria-label="Business card back">
  <p class="brand-name brand-name--small">Flood Rescue 360</p>
  <div class="divider"></div>
  <div class="contact">
    <p class="contact__name">Marcus Pelley</p>
    <p class="contact__title">General Manager</p>
    <ul class="contact__list">
      <li><svg viewBox="0 0 12 12"><rect x="3" y="0.5" width="6" height="11" rx="1.2" fill="none" stroke="#00b0e6" stroke-width="1.2"/><rect x="5" y="9.3" width="2" height="1"/></svg>214-555-0193</li>
      <li><svg viewBox="0 0 12 12"><path d="M2.3 1l2 .3.8 2.4-1.2 1a6 6 0 0 0 3.4 3.4l1-1.2 2.4.8.3 2c-.1.6-.6 1-1.2 1A9.7 9.7 0 0 1 1.3 2.2c0-.6.4-1.1 1-1.2z"/></svg>469-555-0148</li>
      <li><svg viewBox="0 0 12 12"><path d="M0.5 2.5h11v7h-11z" fill="none" stroke="#00b0e6" stroke-width="1.2"/><path d="M0.5 2.5 6 7l5.5-4.5" fill="none" stroke="#00b0e6" stroke-width="1.2"/></svg>Marcus@FloodRescue360.example</li>
      <li><svg viewBox="0 0 12 12"><circle cx="6" cy="6" r="5.3" fill="none" stroke="#00b0e6" stroke-width="1.2"/><path d="M.7 6h10.6M6 .7c-2.6 3-2.6 7.6 0 10.6M6 .7c2.6 3 2.6 7.6 0 10.6" fill="none" stroke="#00b0e6" stroke-width="1"/></svg>FloodRescue360.example</li>
    </ul>
  </div>
  <p class="tagline">Urgency for Your Water Emergency!</p>
</section>

<section class="card card--front" aria-label="Business card front">
  <p class="brand-name brand-name--large">Flood Rescue 360</p>
  <div class="services">
    <p class="services__label">SERVICES</p>
    <p class="services__list">
      <span>Water</span><span class="services__sep"></span>
      <span>Fire</span><span class="services__sep"></span>
      <span>Mold</span><span class="services__sep"></span>
      <span>Reconstruction</span>
    </p>
  </div>
</section>

</body>
</html>
```